Business Card for: Bramwell Financial Advisory Services Inc.

provide strategic financial advisory services to companies in the areas of corporate finance, mergers and acquisitions, executive coaching and strategic planning

Target Market(s)

Companies, banks, accountants, lawyers

Industry/Entity Type

High end business consulting in corporate finance, mergers and acquisitions, consulting

Contact Information for Business Card

Name of company, Name: xxxxxx xxxxxx , CEO, - phone number: 1-xxx-xxx-xxxx, - email address,

Requirements
Must have
• Must be professional and simple.
Nice to have
• simple, straight graphics, must give the impression that we are trustworthy, professional, competent
Should not have
• loud colors, loud design features

```html
<!DOCTYPE html>
<html lang="en">
<head>
<meta charset="utf-8">
<title>Bramwell Financial Advisory Services Inc. – Business Card</title>
<link href="https://fonts.googleapis.com/css2?family=Montserrat:wght@400;500;700&display=swap" rel="stylesheet">
<style>
  :root {
    --bg: #e9e7e4;
    --charcoal: #333333;
    --ink: #2b2b2b;
    --grey: #6b6b6b;
    --white: #ffffff;
    --blue-deep: #0a74b8;
    --blue-mid: #1d9bd6;
    --blue-light: #4cc6e8;
  }
  * { box-sizing: border-box; margin: 0; padding: 0; }
  html, body { width: 1200px; height: 900px; overflow: hidden; }
  body {
    background: var(--bg);
    font-family: "Montserrat", Arial, sans-serif;
    display: flex;
    flex-direction: column;
    align-items: center;
    justify-content: center;
    gap: 44px;
  }
  .card {
    position: relative;
    width: 665px;
    height: 380px;
    overflow: hidden;
    box-shadow: 0 10px 28px rgba(0,0,0,0.22);
  }

  /* Front */
  .card-front {
    background: var(--charcoal);
    color: var(--white);
    display: flex;
    flex-direction: column;
    align-items: center;
    justify-content: center;
  }
  .front-mark {
    width: 26px; height: 26px;
    border-radius: 50%;
    background: var(--white);
    margin-bottom: 22px;
  }
  .front-name {
    font-weight: 500;
    font-size: 64px;
    letter-spacing: 1px;
    line-height: 1;
  }
  .front-tagline {
    font-weight: 500;
    font-size: 19px;
    letter-spacing: 1.5px;
    margin-top: 12px;
  }

  /* Back */
  .card-back { background: var(--white); }
  .back-wave { position: absolute; inset: 0; }
  .person {
    position: absolute;
    left: 52px; top: 64px;
  }
  .person-name {
    font-size: 30px;
    color: var(--ink);
    font-weight: 500;
    line-height: 1.1;
  }
  .person-name strong { font-weight: 700; }
  .person-role {
    font-size: 18px;
    color: var(--grey);
    margin-top: 4px;
  }
  .brand {
    position: absolute;
    right: 44px; top: 58px;
    text-align: right;
    color: var(--ink);
    font-weight: 500;
  }
  .brand-name { font-size: 44px; line-height: 1; letter-spacing: 0.5px; }
  .brand-tagline { font-size: 12.5px; margin-top: 8px; letter-spacing: 0.4px; }

  .contact {
    position: absolute;
    left: 52px; top: 200px;
    list-style: none;
    display: flex;
    flex-direction: column;
    gap: 8px;
  }
  .contact-item {
    display: flex;
    align-items: center;
    gap: 10px;
    font-size: 17px;
    color: var(--ink);
  }
  .contact-icon { width: 22px; height: 22px; flex: none; }
</style>
</head>
<body>

  <section class="card card-front">
    <span class="front-mark"></span>
    <div class="front-name">Bramwell</div>
    <div class="front-tagline">Financial Advisory Services Inc.</div>
  </section>

  <section class="card card-back">
    <svg class="back-wave" viewBox="0 0 665 380" preserveAspectRatio="none">
      <defs>
        <linearGradient id="swoosh" x1="0" y1="0" x2="1" y2="0">
          <stop offset="0" stop-color="var(--blue-deep)"/>
          <stop offset="0.55" stop-color="var(--blue-mid)"/>
          <stop offset="1" stop-color="var(--blue-light)"/>
        </linearGradient>
      </defs>
      <path d="M0,300 C170,318 330,285 470,212 C350,288 180,332 0,332 Z" fill="url(#swoosh)"/>
      <path d="M0,380 L0,342 C200,346 350,300 480,232 C560,190 620,172 665,166 L665,380 Z" fill="var(--charcoal)"/>
    </svg>

    <div class="person">
      <div class="person-name">Daniel <strong>Hartley</strong></div>
      <div class="person-role">Managing Director</div>
    </div>

    <div class="brand">
      <div class="brand-name">Bramwell</div>
      <div class="brand-tagline">Financial Advisory Services Inc.</div>
    </div>

    <ul class="contact">
      <li class="contact-item">
        <svg class="contact-icon" viewBox="0 0 22 22">
          <rect width="22" height="22" rx="4" fill="var(--blue-light)"/>
          <path d="M7 5.5 L9 5.5 L10 8.5 L8.6 9.6 C9.3 11.2 10.6 12.6 12.3 13.4 L13.4 12 L16.4 13 L16.4 15 C16.4 15.8 15.7 16.5 14.9 16.5 C9.9 16.2 5.8 12.1 5.5 7.1 C5.5 6.2 6.2 5.5 7 5.5 Z" fill="var(--white)"/>
        </svg>
        044-555 018 246
      </li>
      <li class="contact-item">
        <svg class="contact-icon" viewBox="0 0 22 22">
          <rect width="22" height="22" rx="4" fill="var(--blue-mid)"/>
          <rect x="5" y="7" width="12" height="8.5" fill="none" stroke="var(--white)" stroke-width="1.4"/>
          <path d="M5 7 L11 12 L17 7" fill="none" stroke="var(--white)" stroke-width="1.4"/>
        </svg>
        info@bramwelladvisory.com
      </li>
      <li class="contact-item">
        <svg class="contact-icon" viewBox="0 0 22 22">
          <rect width="22" height="22" rx="4" fill="var(--blue-deep)"/>
          <circle cx="11" cy="11" r="5.8" fill="none" stroke="var(--white)" stroke-width="1.3"/>
          <ellipse cx="11" cy="11" rx="2.6" ry="5.8" fill="none" stroke="var(--white)" stroke-width="1.1"/>
          <path d="M5.2 11 H16.8 M6.2 8 H15.8 M6.2 14 H15.8" stroke="var(--white)" stroke-width="1"/>
        </svg>
        www.bramwelladvisory.com
      </li>
    </ul>
  </section>

</body>
</html>
```